Business card for medical clinic

I need an upmarket, modern medical/health business card for my clinic

Contact Information for Business Card

name, address, email, qr code

```html
<!DOCTYPE html>
<html lang="en">
<head>
<meta charset="utf-8">
<title>Meridian Care Clinic – Business Card</title>
<link rel="stylesheet" href="https://fonts.googleapis.com/css2?family=Crimson+Text:wght@400;600&display=swap">
<style>
  :root {
    --backdrop: #2b2c2e;
    --card-dark: #171c28;
    --card-mid: #222938;
    --brand-blue: #1f8fd6;
    --brand-steel: #3a6f96;
    --text-light: #e6e9ee;
    --icon-blue: #2a86c8;
  }
  * { box-sizing: border-box; margin: 0; padding: 0; }
  html, body {
    width: 1200px; height: 852px; overflow: hidden;
    background: var(--backdrop);
    font-family: "Crimson Text", Georgia, serif;
  }
  .stage {
    width: 1200px; height: 852px;
    display: flex; align-items: center; justify-content: center; gap: 40px;
  }
  .card {
    position: relative;
    width: 540px; height: 310px;
    border-radius: 22px;
    background: linear-gradient(135deg, var(--card-mid) 0%, var(--card-dark) 100%);
    box-shadow: 0 10px 24px rgba(0,0,0,0.45);
    color: var(--text-light);
    overflow: hidden;
  }
  /* Front */
  .card--front .brand {
    position: absolute; inset: 0;
    display: flex; align-items: center; justify-content: center; gap: 14px;
  }
  .brand__dot {
    width: 28px; height: 28px; border-radius: 50%;
    background: var(--brand-steel); flex: none;
  }
  .brand__name {
    font-size: 32px; font-weight: 600; letter-spacing: 2px;
    text-transform: uppercase; color: var(--brand-steel); white-space: nowrap;
  }
  /* Back */
  .card--back .brand {
    position: absolute; left: 40px; top: 62px;
    display: flex; align-items: center; gap: 10px;
  }
  .card--back .brand__dot { width: 18px; height: 18px; background: var(--brand-blue); }
  .card--back .brand__name { font-size: 20px; letter-spacing: 1px; color: var(--brand-blue); }
  .person { position: absolute; left: 40px; bottom: 48px; }
  .person__name {
    font-size: 24px; font-weight: 600; letter-spacing: 1px;
    text-transform: uppercase; color: var(--brand-blue); line-height: 1.1;
  }
  .person__role { font-size: 15px; color: var(--text-light); }
  .contact {
    position: absolute; right: 36px; top: 108px;
    list-style: none; font-size: 15px; line-height: 1.45;
  }
  .contact__item { display: flex; align-items: center; gap: 10px; white-space: nowrap; }
  .contact__item svg { width: 12px; height: 12px; fill: var(--icon-blue); flex: none; }
  .contact__address { margin-top: 8px; }
</style>
</head>
<body>
<main class="stage">
  <section class="card card--front" aria-label="Card front">
    <div class="brand">
      <span class="brand__dot"></span>
      <span class="brand__name">Meridian Care Clinic</span>
    </div>
  </section>

  <section class="card card--back" aria-label="Card back">
    <div class="brand">
      <span class="brand__dot"></span>
      <span class="brand__name">Meridian Care Clinic</span>
    </div>

    <ul class="contact">
      <li class="contact__item">
        <svg viewBox="0 0 12 12"><path d="M2 1h2.5l1 3-1.5 1a6 6 0 0 0 3 3l1-1.5 3 1V11c-5 0-9-4-9-9z"/></svg>
        <span>0700-555-01234</span>
      </li>
      <li class="contact__item">
        <svg viewBox="0 0 12 12"><path d="M1 2.5h10v7H1zM1.5 3l4.5 3.5L10.5 3v1L6 7.5 1.5 4z" fill-rule="evenodd"/></svg>
        <span>hello@meridiancare.com</span>
      </li>
      <li class="contact__item">
        <svg viewBox="0 0 12 12"><circle cx="6" cy="6" r="5"/><path d="M1 6h10M6 1v10" stroke="#171c28" stroke-width="0.9"/></svg>
        <span>www.meridiancare.com</span>
      </li>
      <li class="contact__item contact__address">
        <span>18 Alder Row, Fairview, US 40321</span>
      </li>
    </ul>

    <div class="person">
      <p class="person__name">Daniel Hart</p>
      <p class="person__role">Managing Director</p>
    </div>
  </section>
</main>
</body>
</html>
```